Professional Website for Leading Global Private Equity Real Estate Company

The company is a leading global Private Equity Real Estate (PERE). We need a homepage design, an inner page design, and color/font tweaks to the logo (color should be more soothing than current blue used in the logo). The logo website should project the company as global, professional, experienced, trustworthy, accessible, YOUNG, DYNAMIC, hi-tech. PLEASE SEE the attached Design Brief Word Doc for details.

Target Market(s)

institional investors and wealthy private individuals

Industry/Entity Type

Finance

Number of Pages Required

2 page

Font styles to use
Sans Serif
Other font styles liked:
• either like in https://www.ferndalequay.com/ or like in presentations (Montserrat Black & Montserrat Light, Century Gothic, Blair ITC, Almoni Neue DL 4.0 AAA Medium, Almoni DL AAA)

Requirements
Must have
• new color palette that is NOT based on current logo. they want a more soothing color palette than the blue in that logo. the new color palette should project: global, professional, experienced, trustworthy, accessible, YOUNG, DYNAMIC, hi-tech.
Nice to have
• the likes these sites: https://www.ferndalequay.com/ and https://www.tvr.law/

```html
<!DOCTYPE html>
<html lang="en">
<head>
<meta charset="utf-8">
<title>Quellmoor Real Estate</title>
<link href="https://fonts.googleapis.com/css2?family=Montserrat:wght@300;400;600;700;800&family=Roboto:wght@400;500;700&display=swap" rel="stylesheet">
<style>
:root{
  --sky:#2db5ec;
  --ink:#111214;
  --grey:#8c8c8c;
  --text:#6d6e71;
  --band:#d1d3d4;
  --pale:#eff0f2;
  --footer:#141416;
  --forest:#1c4a45;
  --jade:#3a8a72;
  --sand:#b48c62;
  --navy:#144c7c;
  --placeholder:#8a8a8a;
  --white:#fff;
}
*{box-sizing:border-box;margin:0;padding:0}
html,body{width:1200px;height:3906px;overflow:hidden}
body{position:relative;font-family:'Montserrat',sans-serif;color:var(--ink);background:var(--white)}
.abs{position:absolute}
.hero{left:0;top:0;width:1200px;height:658px;background:linear-gradient(160deg,#3c4a52 0%,#59646b 40%,#2c353b 100%)}
.brand{left:111px;top:46px;width:238px;height:32px;border:2px solid var(--white);display:flex;align-items:center;gap:8px;padding-left:8px;color:var(--white);font-weight:600;font-size:14px;letter-spacing:.8px;white-space:nowrap}
.brand i{width:12px;height:12px;background:var(--sky);display:block;flex:none}
.nav{left:410px;top:55px;display:flex;gap:26px;font-size:12px;font-weight:700;color:var(--white)}
.login{left:983px;top:44px;width:103px;height:36px;background:var(--sky);color:var(--white);font-weight:600;font-size:16px;display:flex;align-items:center;justify-content:center}
.hero-title{left:0;top:255px;width:1200px;text-align:center;color:var(--white);font-weight:700;font-size:40px}
.hero-text{left:0;top:322px;width:1200px;text-align:center;color:var(--white);font-weight:700;font-size:15.5px;line-height:27px}
.btn{background:var(--sky);color:var(--white);font-weight:700;font-size:15px;display:flex;align-items:center;justify-content:center;gap:8px}
.h2{font-weight:800;font-size:42px;text-align:center;left:0;width:1200px}
.para{font-weight:300;font-size:14px;line-height:27px;color:var(--text);text-align:center}
.circle{width:136px;height:136px;border-radius:50%;color:var(--white);display:flex;flex-direction:column;align-items:center;justify-content:center;text-align:center;font-weight:700;font-size:17px;line-height:20px}
.circle span{font-weight:300;font-size:18px;margin-top:6px}
.platforms{left:0;top:1315px;width:1200px;height:285px;display:flex}
.tile{width:240px;height:285px;color:var(--white);text-align:center;padding-top:28px}
.tile.sky{background:var(--sky)}
.tile.grey{background:var(--grey)}
.tile.photo{background:linear-gradient(135deg,#3d4248,#7a7f85);position:relative}
.tile h3{font-size:17px;font-weight:700;margin-top:16px}
.tile p{font-size:12.5px;font-weight:300;line-height:20px;margin:12px 14px 0}
.tile .more{font-size:14px;font-weight:700;margin-top:14px;display:flex;justify-content:center;align-items:center;gap:8px}
.photo-label{position:absolute;left:0;bottom:30px;width:240px;font-weight:700;font-size:17px}
.h2l{font-weight:800;font-size:42px;white-space:nowrap}
.body{font-weight:300;font-size:13px;line-height:24px;color:var(--text);text-align:justify}
.img{background:linear-gradient(135deg,#c8ccd0,#6f7780)}
.field{background:var(--white);font-family:'Roboto',sans-serif;font-size:13px;color:var(--placeholder);display:flex;align-items:center;gap:8px;padding-left:20px}
.field svg{flex:none}
.field.soft{background:#f1f2f2;font-size:12px}
.footer{left:0;top:3551px;width:1200px;height:355px;background:var(--footer);color:var(--white);font-family:'Roboto',sans-serif}
.fh{font-weight:700;font-size:18px}
.fl{font-size:14px;line-height:26.5px;color:var(--white)}
</style>
</head>
<body>
<div class="abs hero" role="img" aria-label="Photo of two colleagues working together at a laptop in an office"></div>
<div class="abs brand"><i></i>QUELLMOOR REAL ESTATE</div>
<nav class="abs nav"><span>ABOUT US</span><span>OUR BUSINESSES</span><span>INVESTORS LOBBY</span><span>NEWS</span><span>CONTACT US</span></nav>
<div class="abs login">LOGIN</div>
<h1 class="abs hero-title">ACCELERATING GROWTH</h1>
<p class="abs hero-text">Lorem ipsum dolor sit amet, consectetur adipiscing elit, sed do eiusmod<br>tempor incididunt ut labore et dolore magna aliqua.</p>
<div class="abs btn" style="left:504px;top:403px;width:191px;height:49px">ABOUT US <svg width="15" height="15" viewBox="0 0 16 16"><circle cx="8" cy="8" r="8" fill="#fff"/><path d="M6 4l4 4-4 4" stroke="#2db5ec" stroke-width="2" fill="none"/></svg></div>

<h2 class="abs h2" style="top:708px">ABOUT US</h2>
<p class="abs para" style="left:150px;top:779px;width:900px">Lorem ipsum dolor sit amet, consectetur adipiscing elit, sed do eiusmod tempor incididunt ut labore et dolore magna aliqua. Ut enim ad minim veniam, quis nostrud exercitation ullamco laboris nisi ut aliquip ex ea commodo consequat. Duis aute irure dolor in reprehenderit in cupidatat non proident, sunt in culpa voluptate velit esse cillum dolore eu fugiat nulla pariatur.</p>
<p class="abs para" style="left:150px;top:873px;width:900px">Sed ut perspiciatis unde omnis iste natus error sit voluptatem accusantium doloremque laudantium, totam rem aperiam, eaque ipsa quae ab illo inventore veritatis et quasi architecto beatae vitae dicta sunt explicabo. Nemo enim ipsam voluptatem quia voluptas sit aspernatur quia consequuntur magni dolores eos qui ratione voluptatem sequi nesciunt.</p>
<div class="abs circle" style="left:184px;top:998px;background:var(--forest)">Real Estate<span>$279B</span></div>
<div class="abs circle" style="left:383px;top:998px;background:var(--jade)">Private<br>Equity<span>$279B</span></div>
<div class="abs circle" style="left:581px;top:998px;background:var(--sand)">Hedge Fund<br>Solutions<span>$279B</span></div>
<div class="abs circle" style="left:780px;top:998px;background:var(--navy)">Credit &amp;<br>Insurance<span>$279B</span></div>

<h2 class="abs h2" style="top:1222px;font-size:40px">OUR INVESTMENT PLATFORMS</h2>
<section class="abs platforms">
  <div class="tile sky"><svg width="56" height="52" viewBox="0 0 56 52" fill="none" stroke="#fff" stroke-width="2"><rect x="6" y="14" width="16" height="34"/><rect x="22" y="6" width="12" height="42"/><circle cx="40" cy="38" r="10"/><path d="M2 48h52"/></svg><h3>Lorem ipsum amet</h3><p>Sed ut perspiciatis unde omnis iste natus error sit voluptatem accusantium laudantium, totam rem aperiam, eaque ab</p><div class="more">LEARN MORE <svg width="13" height="13" viewBox="0 0 16 16"><circle cx="8" cy="8" r="8" fill="#fff"/><path d="M6 4l4 4-4 4" stroke="#2db5ec" stroke-width="2" fill="none"/></svg></div></div>
  <div class="tile grey"><svg width="56" height="52" viewBox="0 0 56 52" fill="none" stroke="#fff" stroke-width="2"><rect x="6" y="34" width="6" height="14"/><rect x="16" y="26" width="6" height="22"/><rect x="26" y="18" width="6" height="30"/><path d="M6 24L30 6M22 6h8v8"/><circle cx="42" cy="40" r="9"/></svg><h3>Lorem ipsum amet</h3><p>Sed ut perspiciatis unde omnis iste natus error sit voluptatem accusantium laudantium, totam rem aperiam, eaque ab</p><div class="more">LEARN MORE <svg width="13" height="13" viewBox="0 0 16 16"><circle cx="8" cy="8" r="8" fill="#fff"/><path d="M6 4l4 4-4 4" stroke="#8c8c8c" stroke-width="2" fill="none"/></svg></div></div>
  <div class="tile photo" role="img" aria-label="Photo of two colleagues reviewing a tablet"><div class="photo-label">Lorem ipsum amet</div></div>
  <div class="tile grey"><svg width="56" height="52" viewBox="0 0 56 52" fill="none" stroke="#fff" stroke-width="2"><rect x="8" y="4" width="40" height="24"/><path d="M4 40l12-8h10l8 6 8-6h10"/><path d="M14 12h28M14 20h20"/></svg><h3>Lorem ipsum amet</h3><p>Sed ut perspiciatis unde omnis iste natus error sit voluptatem accusantium laudantium, totam rem aperiam, eaque ab</p><div class="more">LEARN MORE <svg width="13" height="13" viewBox="0 0 16 16"><circle cx="8" cy="8" r="8" fill="#fff"/><path d="M6 4l4 4-4 4" stroke="#8c8c8c" stroke-width="2" fill="none"/></svg></div></div>
  <div class="tile sky"><svg width="56" height="52" viewBox="0 0 56 52" fill="none" stroke="#fff" stroke-width="2"><circle cx="28" cy="16" r="12"/><path d="M4 24v14l12 10h8M52 24v14L40 48h-8"/></svg><h3>Lorem ipsum amet</h3><p>Sed ut perspiciatis unde omnis iste natus error sit voluptatem accusantium laudantium, totam rem aperiam, eaque ab</p><div class="more">LEARN MORE <svg width="13" height="13" viewBox="0 0 16 16"><circle cx="8" cy="8" r="8" fill="#fff"/><path d="M6 4l4 4-4 4" stroke="#2db5ec" stroke-width="2" fill="none"/></svg></div></div>
</section>

<h2 class="abs h2l" style="left:111px;top:1709px;font-size:40px">OUR EDGE</h2>
<p class="abs body" style="left:111px;top:1777px;width:426px">Lorem ipsum dolor sit amet, consectetur adipiscing elit, sed do eiusmod tempor incididunt ut labore et dolore magna aliqua. Ut enim ad minim veniam, quis nostrud exercitation ullamco laboris nisi ut aliquip ex ea commodo consequat.</p>
<p class="abs body" style="left:111px;top:1880px;width:426px">Duis aute irure dolor in reprehenderit in voluptate velit esse cillum dolore eu fugiat nulla pariatur. Excepteur sint occaecat cupidatat non proident, sunt in culpa qui officia anim id est laborum.</p>
<div class="abs btn" style="left:111px;top:1981px;width:235px;height:52px;font-size:14px">INVESTOR INFORMATION</div>
<div class="abs img" style="left:599px;top:1688px;width:489px;height:377px" role="img" aria-label="Photo of a team meeting around an office table"></div>

<div class="abs" style="left:0;top:2162px;width:1200px;height:252px;background:var(--band)"></div>
<h2 class="abs h2" style="top:2208px;font-size:40px">STAY UPDATED</h2>
<p class="abs para" style="left:0;top:2254px;width:1200px">Lorem ipsum dolor sit amet, consectetur adipiscing elit, sed do eiusmod</p>
<div class="abs field soft" style="left:188px;top:2312px;width:284px;height:45px">Name</div>
<div class="abs field soft" style="left:493px;top:2312px;width:284px;height:45px">Email Address</div>
<div class="abs btn" style="left:822px;top:2312px;width:190px;height:45px;font-family:'Roboto',sans-serif">SUBMIT NOW</div>

<div class="abs img" style="left:111px;top:2505px;width:488px;height:376px;background:linear-gradient(135deg,#8a939b,#3f4850)" role="img" aria-label="Photo of two colleagues smiling at a laptop"></div>
<h2 class="abs h2l" style="left:658px;top:2530px;font-size:39px">OUR RESPONSIBILITY</h2>
<p class="abs body" style="left:658px;top:2593px;width:428px">Lorem ipsum dolor sit amet, consectetur adipiscing elit, sed do eiusmod tempor incididunt ut labore et dolore magna aliqua. Ut enim ad minim veniam, quis nostrud exercitation ullamco laboris nisi ut aliquip ex ea commodo consequat.</p>
<p class="abs body" style="left:658px;top:2697px;width:428px">Duis aute irure dolor in reprehenderit in voluptate velit esse cillum dolore eu fugiat nulla pariatur. Excepteur sint occaecat cupidatat non proident, sunt in culpa qui officia anim id est laborum.</p>
<div class="abs btn" style="left:658px;top:2799px;width:164px;height:51px">READ MORE</div>

<div class="abs" style="left:0;top:2972px;width:1200px;height:579px;background:var(--pale)"></div>
<h2 class="abs h2" style="top:3015px;font-size:40px">GET IN TOUCH</h2>
<div class="abs field" style="left:152px;top:3105px;width:435px;height:47px"><svg width="11" height="12" viewBox="0 0 12 13" fill="none" stroke="#8a8a8a" stroke-width="1.4"><circle cx="6" cy="4" r="3"/><path d="M1 12c0-3 2-4.5 5-4.5s5 1.5 5 4.5z"/></svg>First Name</div>
<div class="abs field" style="left:613px;top:3105px;width:434px;height:47px"><svg width="11" height="12" viewBox="0 0 12 13" fill="none" stroke="#8a8a8a" stroke-width="1.4"><circle cx="6" cy="4" r="3"/><path d="M1 12c0-3 2-4.5 5-4.5s5 1.5 5 4.5z"/></svg>First Name</div>
<div class="abs field" style="left:152px;top:3181px;width:435px;height:46px"><svg width="12" height="9" viewBox="0 0 14 11"><rect width="14" height="11" fill="#8a8a8a"/><path d="M0 0l7 6 7-6" stroke="#fff" fill="none"/></svg>Email Address</div>
<div class="abs field" style="left:613px;top:3181px;width:434px;height:46px"><svg width="11" height="11" viewBox="0 0 16 16"><path d="M3 1l3 3-2 2a10 10 0 006 6l2-2 3 3-2 2C7 15 1 9 1 3z" fill="#8a8a8a"/></svg>Phone number</div>
<div class="abs field" style="left:152px;top:3256px;width:895px;height:107px;align-items:flex-start;padding-top:16px"><svg width="12" height="11" viewBox="0 0 14 12"><ellipse cx="7" cy="5" rx="7" ry="5" fill="#8a8a8a"/><path d="M2 8l-1 4 4-2z" fill="#8a8a8a"/></svg>Message</div>
<div class="abs btn" style="left:496px;top:3415px;width:208px;height:47px;font-family:'Roboto',sans-serif;font-size:16px">SUBMIT NOW <svg width="15" height="15" viewBox="0 0 16 16"><circle cx="8" cy="8" r="8" fill="#fff"/><path d="M6 4l4 4-4 4" stroke="#2db5ec" stroke-width="2" fill="none"/></svg></div>

<footer class="abs footer">
  <div class="abs" style="left:111px;top:48px"><div class="fh">Important Links</div><div class="fl" style="margin-top:14px">About Us<br>Our Businesses<br>Investors Lobby<br>News<br>Contact Us</div></div>
  <div class="abs" style="left:428px;top:48px"><div class="fh">Explore Quellmoor Real Estate</div><div class="fl" style="margin-top:14px">Privacy and Security<br>Terms of Use<br>Submit Your Story<br>FAQ<br>Support</div></div>
  <div class="abs" style="left:827px;top:48px;width:280px"><div class="fh" style="font-size:17px">Contact Us</div>
    <div style="margin-top:18px;display:flex;gap:12px"><svg width="12" height="16" viewBox="0 0 12 16" style="flex:none"><path d="M6 0a6 6 0 016 6c0 4-6 10-6 10S0 10 0 6a6 6 0 016-6z" fill="#2db5ec"/><circle cx="6" cy="6" r="2" fill="#141416"/></svg><div style="font-size:13px;line-height:18px"><b style="font-size:11px">Location</b><br>921 Lorem ipsum dolor sit consectetur adipiscing elit, sed do eiusmod</div></div>
    <div style="margin-top:12px;display:flex;gap:12px"><svg width="13" height="13" viewBox="0 0 16 16" style="flex:none"><path d="M3 1l3 3-2 2a10 10 0 006 6l2-2 3 3-2 2C7 15 1 9 1 3z" fill="#2db5ec"/></svg><div style="font-size:13px;line-height:18px"><b style="font-size:11px">Phone</b><br>+1 888 888 8888</div></div>
    <div style="margin-top:12px;display:flex;gap:12px"><svg width="14" height="11" viewBox="0 0 14 11" style="flex:none"><rect width="14" height="11" fill="#2db5ec"/><path d="M0 0l7 6 7-6" stroke="#141416" fill="none"/></svg><div style="font-size:13px;line-height:18px"><b style="font-size:11px">Email</b><br>info@quellmoor-re.com</div></div>
  </div>
  <div class="abs" style="left:0;top:312px;width:1200px;text-align:center;font-size:14px">2022 Copyright - Quellmoor Real Estate | All Rights Reserved</div>
</footer>
</body>
</html>
```